National Mission Critical Construction Contractor needs Stationery Design to make a bold statement

We are a small commercial construction company, working primarily in mission critical facilities across the U.S.. We have exciting corporate changes going an and a new logo and office space so we need new stationery. The final design should incorporate our new logo and invoke a fresh, high-tech feel while looking simple and modern.

Industry/Entity Type

Construction

Contact Information for Business Card

We are required to list our state licensing qualifications on the back of our card.

Font styles to use
Sans Serif

Requirements
Must have
• We need to have a design for second page of stationery, envelopes both standard and with a window and for a 3 x 4 notepad.

```html
<!DOCTYPE html>
<html lang="en">
<head>
<meta charset="utf-8">
<title>North Forge – Business Card</title>
<link rel="stylesheet" href="https://fonts.googleapis.com/css2?family=Source+Sans+3:wght@400;600;700&display=swap">
<style>
  :root {
    --backdrop: #3a3a3a;
    --card-white: #f7f7f7;
    --brand-blue: #1a6fc4;
    --name-blue: #1565b8;
    --sky-blue: #2aa0dc;
    --leaf-green: #7cc242;
    --text-grey: #454545;
    --rule-grey: #c8c8c8;
    --white: #ffffff;
  }
  * { box-sizing: border-box; margin: 0; padding: 0; }
  html, body { width: 1200px; height: 750px; overflow: hidden; }
  body {
    background: var(--backdrop);
    font-family: "Source Sans 3", sans-serif;
    position: relative;
  }
  .card {
    position: absolute;
    top: 228px;
    width: 461px;
    height: 263px;
    overflow: hidden;
  }
  .card-front { left: 124px; background: var(--card-white); }
  .card-back { left: 618px; background: var(--brand-blue); }

  .brand { position: absolute; display: flex; align-items: center; gap: 8px; }
  .brand-front { right: 25px; top: 32px; }
  .brand-name {
    font-weight: 600;
    font-size: 24px;
    letter-spacing: 0.5px;
    line-height: 1;
    white-space: nowrap;
  }
  .brand-front .brand-name { color: var(--brand-blue); }
  .brand-dot {
    width: 52px; height: 52px;
    border: 3px solid var(--brand-blue);
    border-radius: 50%;
  }

  .person-name {
    position: absolute; left: 27px; top: 137px;
    font-size: 19px; font-weight: 700; color: var(--name-blue);
  }
  .person-role {
    position: absolute; left: 27px; top: 161px;
    font-size: 14px; color: var(--sky-blue);
  }
  .email {
    position: absolute; right: 30px; top: 170px;
    font-size: 12.5px; color: var(--text-grey);
  }
  .rule {
    position: absolute; left: 27px; top: 189px;
    width: 410px; height: 1px; background: var(--rule-grey);
  }
  .address {
    position: absolute; left: 27px; top: 196px;
    font-size: 12.5px; line-height: 17px; color: var(--text-grey);
  }
  .contact-line {
    position: absolute; display: flex; align-items: center; gap: 5px;
    font-size: 12.5px; color: var(--text-grey); white-space: nowrap;
  }
  .contact-line svg { width: 12px; height: 12px; fill: var(--brand-blue); }

  .colour-bars { position: absolute; left: 0; bottom: 0; width: 100%; height: 10px; display: flex; gap: 2px; }
  .colour-bars span { flex: 1; }
  .bar-green { background: var(--leaf-green); }
  .bar-sky { background: var(--sky-blue); }
  .bar-blue { background: var(--brand-blue); }

  .back-ring {
    position: absolute; left: 12px; top: 10px;
    width: 244px; height: 244px;
    border: 8px solid rgba(255,255,255,0.08);
    border-radius: 50%;
  }
  .brand-back { right: 23px; top: 187px; }
  .brand-back .brand-name { color: var(--white); }
  .back-web {
    position: absolute; right: 23px; top: 225px;
    font-size: 12px; letter-spacing: 3.6px; color: var(--white);
  }
</style>
</head>
<body>
  <section class="card card-front" aria-label="Business card front">
    <div class="brand brand-front">
      <div class="brand-dot"></div>
      <div class="brand-name">NORTH FORGE</div>
    </div>

    <div class="person-name">DANA MORROW</div>
    <div class="person-role">CEO/Founder</div>
    <div class="email">dana@northforge.com</div>
    <div class="rule"></div>

    <div class="address">2140 Harbor View Road<br>Juneau, Alaska 99801</div>

    <div class="contact-line" style="left:192px; top:196px;">
      <svg viewBox="0 0 24 24" aria-hidden="true"><path d="M6.6 10.8a15.1 15.1 0 0 0 6.6 6.6l2.2-2.2a1 1 0 0 1 1-.25 11.4 11.4 0 0 0 3.6.6 1 1 0 0 1 1 1V20a1 1 0 0 1-1 1A17 17 0 0 1 3 4a1 1 0 0 1 1-1h3.5a1 1 0 0 1 1 1c0 1.25.2 2.45.6 3.6a1 1 0 0 1-.25 1z"/></svg>
      555 214 7730
    </div>
    <div class="contact-line" style="left:192px; top:213px;">
      <svg viewBox="0 0 24 24" aria-hidden="true"><path d="M7 1h10a2 2 0 0 1 2 2v18a2 2 0 0 1-2 2H7a2 2 0 0 1-2-2V3a2 2 0 0 1 2-2zm0 3v14h10V4zm5 15.5a1 1 0 1 0 0 2 1 1 0 0 0 0-2z"/></svg>
      555 386 1492
    </div>
    <div class="contact-line" style="left:304px; top:196px;">
      <svg viewBox="0 0 24 24" aria-hidden="true"><path d="M6 2h12v6H6zM3 9h18a2 2 0 0 1 2 2v6h-4v5H5v-5H1v-6a2 2 0 0 1 2-2zm4 8v3h10v-3z"/></svg>
      555 902 4417
    </div>
    <div class="contact-line" style="left:304px; top:213px;">
      <svg viewBox="0 0 24 24" aria-hidden="true"><path d="M12 1a11 11 0 1 0 0 22 11 11 0 0 0 0-22zm-1 19.9A9 9 0 0 1 3.2 10.6L8 15.4v1a2 2 0 0 0 2 2h1zm6.9-2.5A2 2 0 0 0 16 17h-1v-3a1 1 0 0 0-1-1H8v-2h2a1 1 0 0 0 1-1V8h2a2 2 0 0 0 2-2v-.4a9 9 0 0 1 2.9 12.8z"/></svg>
      www.northforge.com
    </div>

    <div class="colour-bars" aria-hidden="true">
      <span class="bar-green"></span><span class="bar-sky"></span><span class="bar-blue"></span>
    </div>
  </section>

  <section class="card card-back" aria-label="Business card back">
    <div class="back-ring" aria-hidden="true"></div>
    <div class="brand brand-back">
      <div class="brand-name">NORTH FORGE</div>
    </div>
    <div class="back-web">www.northforge.com</div>
  </section>
</body>
</html>
```